Redesign Canvas Art E-Commerce Website

Help! I hired a couple of companies on Brisklo.com to build and design an e-commerce website for me. After three long and painful months, I have one that I believe is functional on the back-end, but aesthetically on the front end is a mess.

We are a small family business that will take your digital photo and manipulate it into a digitally created oil, watercolor or impressionist style pieces of artwork that we print on museum quality, gallery grade canvas and ship to the customer, ready to hang.

We are looking to create an e-commerce website where a customer can choose their art style, upload a photo, choose their canvas size and orientation (horizontal or vertical) and checkout. Within 48 hours, we will send them back a proof of their newly created, customized artwork for them to approve or not approve. If they approve, we print, package and ship them the product. If they do not approve, we offer unlimited revisions until they are happy.

As I mentioned, the back end functionality is already there, just need design help. No coding required

Here is a link to the development page that they created: https://plumwickstudio.com/development/

As you can see, it looks off...doesnt line up properly, wasted space, weird font. Feel free to either correct the homepage they created or design an entirely new page. I am attaching some examples of before and after photos of artwork for reference. I also think the testimonials page and shop page can use a little style. The content is there and accurate, it just doesn't look pretty. Please keep in mind that our customers will probably not be very tech savvy. The customers will probably be sending us pics of kids, grandkids, pets, family portraits, vacation photos, etc.

Here is one of our competitors - www.gildavantry.com
Their website looks clean and inviting.

Thank you in advance! Im looking forward to seeing the results. I am including our logo in the attachments (I do not have it in a vector file, just a jpeg)

Target Market(s)

Non tech-savvy indiduals, 30-70 years old

Industry/Entity Type

Please look at https://plumwickstudio.com/development/ to see various pages and what the other designers did

Number of Pages Required

1 page

Requirements
Must have
• Verbiage on pages leave "as is" but feel free to change styles. Would like to keep existing four categories on homepage
Nice to have
• Warm and inviting homepage that evokes emotion

```html
<!DOCTYPE html>
<html lang="en">
<head>
<meta charset="utf-8">
<title>Plumwick Studio – Turn Your Digital Photos Into Wall Art</title>
<link href="https://fonts.googleapis.com/css2?family=Alfa+Slab+One&family=Roboto:wght@400;500;700&display=swap" rel="stylesheet">
<style>
:root{
  --red:#e8202a;
  --orange:#f47c20;
  --green:#2e8b2e;
  --teal:#1fa9c9;
  --blue:#23a9d6;
  --ink:#111111;
  --text:#555555;
  --footer:#141414;
  --grad:linear-gradient(90deg,#13a085 0%,#8a9a16 40%,#f47c20 70%,#e8202a 100%);
  --band:linear-gradient(90deg,#1fb0d2 0%,#3a9a55 25%,#7d8f10 42%,#e07a14 62%,#f47c20 75%,#e8202a 100%);
}
*{box-sizing:border-box;margin:0;padding:0}
html,body{width:1200px;height:4145px;overflow:hidden}
body{position:relative;background:#fff;font-family:"Roboto",Arial,sans-serif;color:var(--ink)}
.abs{position:absolute}
.display{font-family:"Alfa Slab One",Georgia,serif;font-weight:400}
.accent-red{color:var(--red)}
.accent-green{color:var(--green)}
.top-rule{left:0;top:0;width:1200px;height:5px;background:var(--red)}
.btn{position:absolute;display:flex;align-items:center;justify-content:center;border-radius:30px;font-weight:700;font-size:15px;color:#fff;background:var(--grad)}
.btn-outline{background:#fff;color:var(--red);border:3px solid transparent;background-image:linear-gradient(#fff,#fff),var(--grad);background-origin:border-box;background-clip:padding-box,border-box}
.brand{display:flex;align-items:center;gap:12px;font-weight:700;font-size:30px;color:var(--ink)}
.brand-dot{width:34px;height:34px;border-radius:50%;background:var(--orange)}
.nav{top:112px;font-size:17px;font-weight:500}
.nav span{position:absolute;white-space:nowrap}
.hero{left:72px;top:177px;width:1056px;height:570px;border-radius:10px;background:linear-gradient(100deg,#a0542c 0%,#c49a78 30%,#ddd6cf 55%,#e9e6e3 100%)}
.hero-title{right:146px;top:296px;text-align:right;font-size:48px;line-height:60px}
.feature{top:784px;width:335px;height:125px;border-radius:6px;color:#fff;font-weight:700;font-size:17px;line-height:30px}
.feature .icon{position:absolute;left:9px;top:9px;width:96px;height:107px;background:#fff;border-radius:5px;display:flex;align-items:center;justify-content:center}
.feature .label{position:absolute;left:132px;top:32px}
.about-title{left:72px;top:1050px;font-size:42px}
.about-text{left:72px;top:1123px;width:460px;font-size:13px;line-height:27.5px;color:var(--text)}
.about-text p{margin-bottom:27px}
.photo{position:absolute}
.band{left:0;top:1720px;width:1200px;height:608px;background:var(--band)}
.band-title{left:0;top:1783px;width:1200px;text-align:center;font-size:42px;color:#fff}
.cat{top:1874px;width:236px;height:342px;border:3px solid #1a9a8a}
.cat-label{top:2238px;width:236px;text-align:center;color:#fff;font-weight:700;font-size:16px;letter-spacing:.5px}
.form-title{left:661px;top:2494px;font-size:42px;line-height:60px}
.field{position:absolute;border:1px solid #d6d6d6;border-radius:3px;font-size:12px;color:#666;display:flex;align-items:center;padding-left:20px}
.field .caret{position:absolute;right:20px;font-size:10px;color:#999}
.flabel{position:absolute;right:317px;font-size:14px;color:#444;font-weight:500;text-align:right}
.flabel em{color:var(--red);font-style:normal}
.why-title{left:0;top:3245px;width:1200px;text-align:center;font-size:42px}
.why-card{top:3339px;width:335px;height:407px;border-radius:30px;background:#fff;box-shadow:0 8px 24px rgba(0,0,0,.10)}
.why-card .circle{position:absolute;left:114px;top:51px;width:106px;height:106px;border-radius:50%;background:var(--grad);display:flex;align-items:center;justify-content:center}
.why-card h3{position:absolute;top:188px;width:100%;text-align:center;font-family:"Alfa Slab One",Georgia,serif;font-weight:400;font-size:19px}
.why-card p{position:absolute;top:233px;left:36px;right:36px;text-align:center;font-size:13px;line-height:27px;color:var(--text)}
.footer{left:0;top:3831px;width:1200px;height:314px;background:var(--footer);color:#fff}
.footer-nav span{position:absolute;top:163px;font-size:15px;transform:translateX(-50%);white-space:nowrap}
.social{position:absolute;top:213px;width:22px;height:22px;border-radius:50%;background:#f2a81d}
.copyright{position:absolute;top:262px;width:100%;text-align:center;font-size:11px}
</style>
</head>
<body>

<div class="abs top-rule"></div>

<!-- Header -->
<div class="abs brand" style="left:64px;top:70px"><span class="brand-dot"></span>Plumwick Studio</div>
<div class="btn btn-outline" style="left:832px;top:45px;width:137px;height:42px">My Orders</div>
<div class="btn" style="left:985px;top:45px;width:136px;height:42px">Shop Now</div>
<nav class="abs nav" style="left:0;width:1200px">
  <span style="left:454px">Home</span>
  <span style="left:558px">About Us</span>
  <span style="left:688px">Testimonials</span>
  <span style="left:848px">FAQ</span>
  <span style="left:936px">Shop</span>
  <span style="left:1034px">Contact Us</span>
</nav>

<!-- Hero -->
<div class="abs hero" role="img" aria-label="Couple hanging a framed canvas portrait of a bride on a living room wall"></div>
<h1 class="abs hero-title display">Turn Your <span class="accent-red">Digital</span><br><span class="accent-red">Photos</span> Into<br>One of a <span class="accent-green">Kind</span><br><span class="accent-green">Wall Art</span></h1>
<div class="btn" style="left:917px;top:571px;width:137px;height:42px">Shop Now</div>

<!-- Features -->
<div class="abs feature" style="left:72px;background:var(--blue)">
  <div class="icon"><svg width="54" height="54" viewBox="0 0 54 54"><circle cx="27" cy="27" r="25" fill="var(--blue)"/><circle cx="27" cy="27" r="17" fill="none" stroke="#fff" stroke-width="3"/><path d="M19 27l6 6 11-12" fill="none" stroke="#fff" stroke-width="4" stroke-linecap="round" stroke-linejoin="round"/></svg></div>
  <div class="label">Print On Museum<br>Quality</div>
</div>
<div class="abs feature" style="left:433px;background:var(--green)">
  <div class="icon"><svg width="56" height="50" viewBox="0 0 56 50"><rect x="2" y="2" width="52" height="46" rx="5" fill="var(--green)"/><rect x="8" y="14" width="40" height="28" fill="#fff"/><circle cx="9" cy="8" r="2" fill="#fff"/><circle cx="16" cy="8" r="2" fill="#fff"/><circle cx="23" cy="8" r="2" fill="#fff"/><path d="M10 40l10-12 8 8 6-6 12 10z" fill="var(--green)"/><circle cx="18" cy="21" r="3" fill="var(--green)"/></svg></div>
  <div class="label">Gallery Grade<br>Canvas</div>
</div>
<div class="abs feature" style="left:792px;background:var(--orange)">
  <div class="icon"><svg width="64" height="40" viewBox="0 0 64 40"><rect x="10" y="4" width="32" height="24" rx="2" fill="var(--orange)"/><path d="M42 12h10l8 9v7H42z" fill="var(--orange)"/><circle cx="20" cy="31" r="6" fill="var(--orange)" stroke="#fff" stroke-width="2"/><circle cx="50" cy="31" r="6" fill="var(--orange)" stroke="#fff" stroke-width="2"/><rect x="0" y="10" width="14" height="3" fill="var(--orange)"/><rect x="3" y="17" width="11" height="3" fill="var(--orange)"/></svg></div>
  <div class="label">Ship To The Customer<br>Within 48 Hours</div>
</div>

<!-- About -->
<h2 class="abs about-title display">ABOUT <span class="accent-red">US</span></h2>
<div class="abs about-text">
  <p>At Plumwick Studio, we take your digital photo and turn it into a one-of-a-kind piece of artwork!</p>
  <p>The process couldn’t be any easier. Simply upload your photo, choose your art style and size, and let our team of skilled digital artists do the rest. Do you want to put your digital photo on canvas without an art style? No problem! Just choose the “Digital Photo/Retouching” category and upload your photo. We can print your photo “as is” or do some minor retouching (e.g. remove objects, enhance colors, lighten photo, etc)</p>
  <p>You will receive a proof in your email to approve within 1-2 days. Once approved, your customized artwork will be transferred to canvas and shipped from our design studio in Florida.</p>
</div>
<div class="btn" style="left:72px;top:1512px;width:137px;height:42px">Read More</div>
<div class="photo" style="left:660px;top:1017px;width:473px;height:495px;background:linear-gradient(135deg,#f4e7e2,#e6b9a6 50%,#f6efec);box-shadow:0 6px 18px rgba(0,0,0,.12)" role="img" aria-label="Watercolor style portrait of a mother and her baby"></div>
<div class="photo" style="left:566px;top:1327px;width:295px;height:271px;padding:7px;background:linear-gradient(135deg,#1a9a8a,#f47c20 60%,#e8202a)">
  <div style="width:100%;height:100%;border:2px solid #fff;background:linear-gradient(135deg,#d9b8a5,#f1e3dc 60%,#fff)" role="img" aria-label="Photo of a mother holding her baby close"></div>
</div>

<!-- Featured categories -->
<div class="abs band"></div>
<h2 class="abs band-title display">FEATURED CATEGORIES</h2>
<div class="abs cat" style="left:79px;background:linear-gradient(160deg,#3d5a2a,#8d6a4a 50%,#c8b8a4)" role="img" aria-label="Oil painting style wedding portrait of a couple"></div>
<div class="abs cat" style="left:348px;background:linear-gradient(135deg,#f3e1da,#e3ad96 50%,#f6efec)" role="img" aria-label="Watercolor style portrait of a mother and baby">
  <div class="btn" style="left:10px;top:279px;width:210px;height:46px;border-radius:4px;background:var(--red);font-size:15px">Get Started</div>
</div>
<div class="abs cat" style="left:616px;background:linear-gradient(160deg,#3a1e12,#8a5a3a 45%,#c7c77a)" role="img" aria-label="Impressionist style portrait of a bride with a bouquet"></div>
<div class="abs cat" style="left:885px;background:linear-gradient(160deg,#f2f2f2,#b5a898 45%,#6f8a78)" role="img" aria-label="Digital photo of a smiling grandparent couple"></div>
<div class="abs cat-label" style="left:79px;border:0">OIL PAINTING</div>
<div class="abs cat-label" style="left:348px">WATERCOLOR</div>
<div class="abs cat-label" style="left:616px">IMPRESSIONIST</div>
<div class="abs cat-label" style="left:885px">DIGITAL PHOTO</div>

<!-- Order form -->
<div class="photo" style="left:95px;top:2463px;width:499px;height:681px;padding:3px;background:linear-gradient(160deg,#e8202a,#f47c20 50%,#1a9a8a)">
  <div style="width:100%;height:100%;background:linear-gradient(160deg,#b9d6ea 0%,#7a3e1c 35%,#c0661e 55%,#2a2220 75%,#b9d6ea 100%)" role="img" aria-label="Impressionist painting of a horse and rider jumping"></div>
</div>
<h2 class="abs form-title display">FROM<br>PHOTO TO <span class="accent-red">MUSEUM</span><br><span class="accent-red">QUALITY CANVAS ART</span></h2>
<div class="abs" style="left:661px;top:2683px;font-size:15px;color:#666">Customized Photo To Impressionist</div>
<div class="field" style="left:661px;top:2724px;width:443px;height:52px">Upload Your Photo Here
  <svg class="caret" width="16" height="12" viewBox="0 0 16 12"><path d="M4 11a3.5 3.5 0 0 1 0-7 5 5 0 0 1 9 1.5A2.8 2.8 0 0 1 12 11z" fill="#aaa"/></svg></div>
<div class="flabel" style="top:2806px">Style <em>*</em></div>
<div class="field" style="left:911px;top:2795px;width:193px;height:42px">Impressionist<span class="caret">▼</span></div>
<div class="flabel" style="top:2869px">Size <em>*</em></div>
<div class="field" style="left:911px;top:2858px;width:193px;height:42px">20" X 30" (USD 129.00)<span class="caret">▼</span></div>
<div class="flabel" style="top:2932px">Orientation <em>*</em></div>
<div class="field" style="left:911px;top:2920px;width:193px;height:44px">Portrait (Vertical)<span class="caret">▼</span></div>
<div class="flabel" style="top:2996px">Notes To Artist</div>
<div class="field" style="left:911px;top:2983px;width:193px;height:45px"></div>
<div class="btn" style="left:969px;top:3063px;width:136px;height:42px">Shop Now</div>

<!-- Why choose us -->
<h2 class="abs why-title display">WHY CHOOSE <span class="accent-red">US</span></h2>
<div class="abs why-card" style="left:72px">
  <div class="circle"><svg width="50" height="50" viewBox="0 0 50 50" fill="none" stroke="#fff" stroke-width="3" stroke-linecap="round"><path d="M25 13a10 10 0 0 1 6 18v4H19v-4a10 10 0 0 1 6-18z" fill="#fff"/><path d="M20 40h10M21 44h8M25 3v5M8 10l4 4M42 10l-4 4M3 25h5M42 25h5"/></svg></div>
  <h3>YOUR IDEA YOUR DESIGN</h3>
  <p>Each art piece is customized for you! You choose your size, orientation and art style. Makes a perfect gift!!!</p>
</div>
<div class="abs why-card" style="left:433px">
  <div class="circle"><svg width="56" height="36" viewBox="0 0 64 40"><rect x="10" y="4" width="32" height="24" rx="2" fill="#fff"/><path d="M42 12h10l8 9v7H42z" fill="#fff"/><circle cx="20" cy="31" r="6" fill="#fff" stroke="#f47c20" stroke-width="2"/><circle cx="50" cy="31" r="6" fill="#fff" stroke="#f47c20" stroke-width="2"/><rect x="0" y="10" width="14" height="3" fill="#fff"/><rect x="3" y="17" width="11" height="3" fill="#fff"/></svg></div>
  <h3>FAST SHIPPING</h3>
  <p>Your artwork is printed and shipped in the USA! We offer fast turnaround with transit times typically 3-7 days. Free tracking with each order!!</p>
</div>
<div class="abs why-card" style="left:793px">
  <div class="circle"><svg width="52" height="52" viewBox="0 0 54 54"><circle cx="27" cy="27" r="24" fill="#fff"/><circle cx="27" cy="27" r="15" fill="none" stroke="#f47c20" stroke-width="3"/><path d="M20 27l5 5 10-11" fill="none" stroke="#f47c20" stroke-width="4" stroke-linecap="round" stroke-linejoin="round"/></svg></div>
  <h3>HIGH QUALITY</h3>
  <p>We’ve put a lot of effort ensuring your artwork is of the highest quality. Each piece is printed on the highest quality, gallery grade canvas. It is ready to hang upon arrival.!</p>
</div>

<!-- Footer -->
<footer class="abs footer">
  <div class="brand" style="position:absolute;left:0;width:1200px;top:70px;justify-content:center;color:#fff"><span class="brand-dot"></span>Plumwick Studio</div>
  <div class="footer-nav">
    <span style="left:340px">Home</span>
    <span style="left:438px">About Us</span>
    <span style="left:560px">Testimonials</span>
    <span style="left:663px">FAQ</span>
    <span style="left:740px">Shop</span>
    <span style="left:842px">Contact Us</span>
  </div>
  <span class="social" style="left:544px"></span>
  <span class="social" style="left:573px"></span>
  <span class="social" style="left:604px"></span>
  <span class="social" style="left:634px"></span>
  <div class="copyright">© Copyright 2023 | All Rights Reserved</div>
</footer>

</body>
</html>
```